Young, dynamic furniture company needs a new business card design

We require a new business card design for our modern furniture company which supplies furniture and appliances to the property and development market.
Oakridge Interiors has become one of the leading furniture & appliance suppliers to the property market withing London. With over 10 years experience, we have increased our business to supply not only private landlords and managing agents, but also property developers, housing associations and local councils.
We offer not only a complete range of furniture which includes beds, wardrobes, dining sets and sofas, but also a high quality, full delivery and assembly service to help you with all our furnishing needs.

Target Market(s)

Private landlords, estate agents, letting agents, property management companies

Industry/Entity Type

Business

Contact Information for Business Card

Name,
Title,
Address,
Mobile,
Telephone,
Fax, Website, email address

Font styles to use
Sans Serif

Colors
3176b5
0555a3
85abd2
cfdeed

Requirements
Must have
• All the above information for each of our staff, along with our logo

```html
<!DOCTYPE html>
<html lang="en">
<head>
<meta charset="utf-8">
<title>Oakridge Interiors – Business Card</title>
<link href="https://fonts.googleapis.com/css2?family=Open+Sans:wght@400;600;700&display=swap" rel="stylesheet">
<style>
  :root {
    --backdrop: #2b2c2f;
    --paper: #ffffff;
    --brand-deep: #0555a3;
    --brand-mid: #3176b5;
    --brand-soft: #85abd2;
    --brand-pale: #cfdeed;
    --ink: #2e2e33;
    --ink-muted: #6b6f76;
  }
  * { margin: 0; padding: 0; box-sizing: border-box; }
  html, body { width: 1200px; height: 843px; overflow: hidden; }
  body {
    background: var(--backdrop);
    font-family: "Open Sans", Arial, sans-serif;
    position: relative;
  }
  .card {
    position: absolute;
    top: 273px;
    width: 520px;
    height: 297px;
    background: var(--paper);
    overflow: hidden;
  }
  .card--back { left: 60px; }
  .card--front { left: 620px; }

  /* Back side */
  .back-identity {
    position: absolute;
    inset: 0;
    display: flex;
    flex-direction: column;
    align-items: center;
    justify-content: center;
    gap: 8px;
  }
  .brand-line {
    display: flex;
    align-items: center;
    gap: 10px;
  }
  .brand-dot {
    width: 16px; height: 16px;
    border-radius: 50%;
    background: var(--brand-mid);
  }
  .brand-name {
    font-weight: 700;
    font-size: 26px;
    color: var(--ink);
    letter-spacing: 0.5px;
    text-transform: uppercase;
  }
  .brand-tagline {
    font-size: 10px;
    letter-spacing: 2.5px;
    text-transform: uppercase;
    color: var(--ink-muted);
  }

  /* Front side */
  .front-art { position: absolute; inset: 0; }
  .front-brand {
    position: absolute;
    left: 24px;
    top: 36px;
    display: flex;
    align-items: center;
    gap: 8px;
  }
  .front-brand .brand-mark {
    width: 12px; height: 12px;
    background: var(--brand-deep);
  }
  .front-brand .brand-name {
    font-size: 19px;
    color: var(--brand-deep);
  }
  .contact {
    position: absolute;
    right: 22px;
    top: 92px;
    text-align: right;
    color: var(--paper);
  }
  .contact-name {
    font-size: 16px;
    font-weight: 700;
    letter-spacing: 0.6px;
    text-transform: uppercase;
  }
  .contact-title {
    font-size: 12px;
    letter-spacing: 0.6px;
    text-transform: uppercase;
    margin-bottom: 14px;
  }
  .contact-address {
    font-size: 12px;
    line-height: 15px;
    margin-bottom: 6px;
  }
  .contact-list { list-style: none; }
  .contact-list li {
    display: flex;
    justify-content: flex-end;
    align-items: center;
    gap: 6px;
    font-size: 12px;
    line-height: 16px;
  }
  .contact-list svg { width: 11px; height: 11px; fill: var(--paper); flex: none; }
</style>
</head>
<body>

<section class="card card--back" aria-label="Card back">
  <div class="back-identity">
    <div class="brand-line">
      <span class="brand-dot"></span>
      <span class="brand-name">Oakridge Interiors</span>
    </div>
    <p class="brand-tagline">Trade Furnishing Solutions</p>
  </div>
</section>

<section class="card card--front" aria-label="Card front">
  <svg class="front-art" viewBox="0 0 520 297" preserveAspectRatio="none" aria-hidden="true">
    <defs>
      <linearGradient id="front-blue" x1="0" y1="1" x2="1" y2="0">
        <stop offset="0" stop-color="#3176b5"/>
        <stop offset="0.55" stop-color="#0555a3"/>
        <stop offset="1" stop-color="#1a6cbc"/>
      </linearGradient>
    </defs>
    <polygon points="330,0 520,0 520,297 120,297" fill="url(#front-blue)"/>
    <line x1="330" y1="0" x2="120" y2="297" stroke="#ffffff" stroke-width="3"/>
  </svg>

  <div class="front-brand">
    <span class="brand-mark"></span>
    <span class="brand-name">Oakridge Interiors</span>
  </div>

  <div class="contact">
    <p class="contact-name">Daniel Marsh</p>
    <p class="contact-title">President</p>
    <p class="contact-address">412 Harrow Lane<br>Kingston, NY 11020</p>
    <ul class="contact-list">
      <li>555 0142 7781
        <svg viewBox="0 0 12 12"><path d="M1 4c0-1 1-2 5-2s5 1 5 2v1H8.5V4h-5v1H1zM3 6h6l1.5 4.5h-9z"/></svg>
      </li>
      <li>555 0198 3346
        <svg viewBox="0 0 12 12"><path d="M3.5 0h5a1 1 0 0 1 1 1v10a1 1 0 0 1-1 1h-5a1 1 0 0 1-1-1V1a1 1 0 0 1 1-1zm.5 1.5v8h4v-8zM6 10.2a.6.6 0 1 0 0 1.2.6.6 0 0 0 0-1.2z"/></svg>
      </li>
      <li>555 0173 9920
        <svg viewBox="0 0 12 12"><path d="M3 0h6v3H3zM1 4h10v6H9v2H3v-2H1zm3 4v3h4V8z"/></svg>
      </li>
      <li>daniel@oakridge.test
        <svg viewBox="0 0 12 12"><path d="M0 2h12v1L6 7 0 3zm0 2.3 6 4 6-4V10H0z"/></svg>
      </li>
      <li>www.oakridge.test
        <svg viewBox="0 0 12 12"><path d="M6 0a6 6 0 1 0 0 12A6 6 0 0 0 6 0zm0 1.3c.8 0 1.6 1.6 1.8 3.7H4.2C4.4 2.9 5.2 1.3 6 1.3zM4.2 7h3.6C7.6 9.1 6.8 10.7 6 10.7S4.4 9.1 4.2 7z"/></svg>
      </li>
    </ul>
  </div>
</section>

</body>
</html>
```